Business Card Design for Marketing Firm

Looking for business card design for higher end marketing firm. Clean but impressionable/trendy. We are a marketing firm that represents manufacturers in the foodservice equipment and supply industry. Our customers are end users such has hotels, restaurants, country clubs, convention centers and casinos as well as distributors of restaurants supplies and equipment, and manufacturers of foodservice equipment and supplies.
Target Market(s)
Hotels, Restaurants, Supply & Equipment Distributors, Foodservice Manufacturers
Industry/Entity Type
Foodservice/Hospitality
Contact Information for Business Card
Name, Title, Contact Number, Email, Website, Social Media, Address
Requirements
Must have
- Clean & Simple but Serious and Impressionable

```html
<!DOCTYPE html>
<html lang="en">
<head>
<meta charset="utf-8">
<title>Larkfield Trade Group – Business Card</title>
<link rel="stylesheet" href="https://fonts.googleapis.com/css2?family=Noto+Serif:wght@700&family=Arimo:wght@400&display=swap">
<style>
  :root {
    --navy: #272c6b;
    --paper: #f3f3f3;
    --ink: #2b2b2b;
    --backdrop: #1c1c1c;
    --white: #ffffff;
  }
  * { margin: 0; padding: 0; box-sizing: border-box; }
  html, body { width: 1200px; height: 1059px; overflow: hidden; background: var(--backdrop); }
  .canvas { position: relative; width: 1200px; height: 1059px; }

  .card { position: absolute; border-radius: 18px; overflow: hidden; }
  .card-front { left: 257px; top: 89px; width: 687px; height: 390px; background: var(--paper); color: var(--ink); }
  .card-back { left: 254px; top: 547px; width: 693px; height: 394px; background: var(--navy); }

  .brand { position: absolute; display: flex; align-items: center; gap: 10px; font-family: "Arimo", sans-serif; font-weight: 400; white-space: nowrap; }
  .brand-square { display: block; }
  .card-front .brand { left: 37px; top: 118px; font-size: 22px; color: var(--navy); }
  .card-front .brand-square { width: 16px; height: 16px; background: var(--navy); }
  .card-back .brand { left: 0; right: 0; top: 176px; justify-content: center; font-size: 36px; color: var(--white); }
  .card-back .brand-square { width: 24px; height: 24px; background: var(--white); }

  .name-marker { position: absolute; left: 0; top: 197px; width: 18px; height: 39px; background: var(--navy); }
  .person-name { position: absolute; left: 37px; top: 190px; font-family: "Noto Serif", serif; font-weight: 700; font-size: 25px; line-height: 1.2; color: var(--navy); letter-spacing: 0.01em; }
  .person-title { position: absolute; left: 37px; top: 221px; font-family: "Arimo", sans-serif; font-size: 16px; color: var(--ink); }

  .contact-list { position: absolute; left: 37px; top: 264px; list-style: none; font-family: "Arimo", sans-serif; font-size: 16px; color: var(--ink); }
  .contact-list li { display: flex; align-items: center; height: 23.5px; }
  .contact-list svg { width: 13px; height: 13px; margin-right: 6px; fill: var(--navy); }
  .social-dot { width: 12px; height: 12px; border-radius: 50%; background: var(--navy); margin-right: 6px; }

  .address { position: absolute; right: 33px; top: 314px; text-align: right; font-family: "Arimo", sans-serif; font-style: normal; font-size: 16px; line-height: 21px; color: var(--ink); }
  .footer-bar { position: absolute; left: 451px; bottom: 0; width: 203px; height: 10px; background: var(--navy); }
</style>
</head>
<body>
<main class="canvas">
  <section class="card card-front" aria-label="Business card front">
    <div class="brand"><span class="brand-square"></span>Larkfield Trade Group</div>
    <div class="name-marker"></div>
    <h1 class="person-name">DANIEL WHITFORD</h1>
    <p class="person-title">CEO/Founder</p>
    <ul class="contact-list">
      <li><svg viewBox="0 0 16 16"><path d="M3 1h3l1.5 4-2 1.2a9 9 0 0 0 4.3 4.3L11 8.5l4 1.5v3a2 2 0 0 1-2 2C6.4 15 1 9.6 1 3a2 2 0 0 1 2-2z"/></svg>555-014-2290</li>
      <li><svg viewBox="0 0 16 16"><path d="M1 3h14v10H1z M2 4l6 5 6-5" fill="none" stroke="#272c6b" stroke-width="1.6"/></svg>hello@larkfieldtradegroup.com</li>
      <li><svg viewBox="0 0 16 16"><circle cx="8" cy="8" r="6.5" fill="none" stroke="#272c6b" stroke-width="1.6"/><path d="M1.5 8h13M8 1.5c-3 3.5-3 9.5 0 13M8 1.5c3 3.5 3 9.5 0 13" fill="none" stroke="#272c6b" stroke-width="1.2"/></svg>www.larkfieldtradegroup.com</li>
      <li><span class="social-dot"></span>@larkfieldtrade</li>
    </ul>
    <address class="address">480 Harbor Lane, Suite 210<br>Eastfield, AB 40218</address>
    <div class="footer-bar"></div>
  </section>

  <section class="card card-back" aria-label="Business card back">
    <div class="brand"><span class="brand-square"></span>Larkfield Trade Group</div>
  </section>
</main>
</body>
</html>
```